Web Design job - Condo Debts Collection Business needs a Web Design

I need a site for a client, who works with condo debts collection, and ensure all revenues provided by condo fees will be always available to the building manager of condo on a specific date, regardless of defaults.
I have the visual identity (logo, slogan and colors) of the company, and some requirements on layout (kind of slider, menu options, phone number on a noble position, etc) - maybe I can do a sketch, but I like the idea of give some freedom to designer.

*** PLEASE, we have no interest in templates. We want something new***

Target Market(s)

I have two targets for this design: - Condominium's building manager. This target is looking for a solution to overdue debts on it's condo. - Residents on condominiums. This target wants to live in a better place, where their neighbors pay their condominium fees on time.

Number of Pages Required

1 page

Requirements
Must have
• - Slider with title, some short text related, a nice image (I prefer happy and/or peaceful family, people doing business, happy friends, and so on).
• - I have a special attention to menu. I'm looking for one I can have a nice effect, more elegant, charming, kind of innovative.
• - Phone number on the top (or clearly visible).
• - Member log in area or icon on the top (or clearly visible).
• - News/articles area.
• - Modern fonts, with good quality, sans-serif on areas where reading is more intensive (prefer Google web-fonts).
• - Colors specified on attached files.
Nice to have
• - Clear background color, cause it's better to read larger texts (like articles). Dark backgrounds makes reading difficult.
• - A site with effects (like shadows, lines, curves, gradients, lights) is usually pretty.
• - I pay attention on beautiful footers.
Should not have
• - Images with a lot of money (I don't sell richness, I sell tranquility, peace, harmony, safety).
• - Poor menu.

```html
<!DOCTYPE html>
<html lang="en">
<head>
<meta charset="utf-8">
<title>Condara – Condo Revenue Care</title>
<link rel="stylesheet" href="https://fonts.googleapis.com/css2?family=Playfair+Display:wght@400;700&family=Lato:wght@400;700&display=swap">
<style>
:root{
  --gold:#e3a21a;
  --gold-dark:#c98a0e;
  --ink:#2b2b2b;
  --muted:#8a8a8a;
  --light:#efefef;
  --dark:#1d1d1f;
  --white:#ffffff;
}
*{box-sizing:border-box;margin:0;padding:0}
html,body{width:1200px;height:4164px;overflow:hidden}
body{position:relative;background:var(--white);font-family:"Lato",sans-serif;color:var(--ink)}
.serif{font-family:"Playfair Display",serif}
.abs{position:absolute}
.btn{position:absolute;display:flex;align-items:center;justify-content:center;border-radius:22px;font-size:13px;font-weight:700;letter-spacing:.5px;text-transform:uppercase}
.btn-gold{background:var(--gold);color:var(--white)}
.btn-ghost{border:2px solid var(--white);color:var(--white)}
.mark{position:absolute;width:14px;height:14px;border-left:3px solid var(--gold);border-bottom:3px solid var(--gold);transform:rotate(-45deg)}

/* hero */
.hero{position:absolute;left:0;top:0;width:1200px;height:760px;background:linear-gradient(180deg,#3b3530 0%,#8a6a4c 45%,#5a4030 75%,#2e2824 100%)}
.hero::after{content:"";position:absolute;inset:0;background:rgba(0,0,0,.25)}
.brand{position:absolute;left:100px;top:60px;display:flex;align-items:center;gap:12px;z-index:2;color:var(--white);font-size:40px;font-weight:700}
.brand-square{width:34px;height:34px;background:var(--white)}
.topbar{position:absolute;right:100px;top:62px;display:flex;align-items:center;gap:28px;z-index:2;color:var(--white);font-size:15px;font-weight:700}
.topbar .phone{display:flex;align-items:center;gap:8px}
.login{display:flex;align-items:center;gap:10px;background:var(--gold);border-radius:24px;padding:6px 18px 6px 6px;font-size:13px}
.login i{width:34px;height:34px;border-radius:50%;background:var(--white);display:flex;align-items:center;justify-content:center}
.hero-title{position:absolute;left:0;width:1200px;top:400px;text-align:center;z-index:2;color:var(--white);font-size:84px;font-weight:400;letter-spacing:2px}
.hero-sub{position:absolute;left:0;width:1200px;top:528px;text-align:center;z-index:2;color:var(--white);font-size:15px}
.arrow{position:absolute;top:390px;width:40px;height:40px;border-radius:50%;background:rgba(255,255,255,.25);z-index:2}

/* menu */
.menu{position:absolute;left:120px;top:735px;width:960px;height:56px;background:var(--gold);clip-path:polygon(24px 0,936px 0,960px 28px,936px 56px,24px 56px,0 28px);display:flex;align-items:center;padding-left:60px;gap:44px;color:var(--white);font-size:16px;z-index:3}
.menu-shadow{position:absolute;left:180px;top:790px;width:840px;height:40px;background:radial-gradient(ellipse at top,rgba(0,0,0,.22),transparent 70%)}
.search{position:absolute;left:680px;top:14px;width:220px;height:28px;background:var(--white);border-radius:14px;color:#aaa;font-size:12px;padding:6px 14px}

/* about */
.h2{position:absolute;font-family:"Playfair Display",serif;font-size:48px;font-weight:700;color:var(--ink)}
.body-text{position:absolute;font-size:14px;line-height:26px;color:var(--muted)}
.photo{position:absolute}
.frame{position:absolute;border:3px solid var(--gold)}

/* news */
.news-band{position:absolute;left:0;top:1540px;width:1200px;height:1000px;background:var(--light);clip-path:polygon(0 80px,1200px 0,1200px 1000px,0 1000px)}
.card{position:absolute;background:var(--white);box-shadow:0 4px 18px rgba(0,0,0,.10)}
.card h3{font-size:17px;font-weight:700;color:var(--ink);line-height:24px}
.date{display:flex;align-items:center;gap:8px;color:var(--gold);font-size:12px;margin:10px 0}
.date::before{content:"";width:12px;height:12px;background:var(--gold);border-radius:2px}
.card p{font-size:12px;line-height:20px;color:var(--muted)}

/* contact */
.dark{position:absolute;left:0;top:3050px;width:1200px;height:560px;background:linear-gradient(120deg,#17171a,#2a2a2e);clip-path:polygon(0 60px,1200px 0,1200px 560px,0 560px)}
.contact-item{position:absolute;display:flex;align-items:center;gap:18px;color:#cfcfcf;font-size:13px;line-height:22px}
.contact-item i{width:44px;height:44px;border-radius:50%;border:2px solid #666;display:flex;align-items:center;justify-content:center;flex:none}
.form{position:absolute;left:775px;top:2965px;width:330px;height:530px;background:var(--white);box-shadow:0 8px 30px rgba(0,0,0,.2);padding:44px 28px}
.form h3{font-family:"Playfair Display",serif;font-size:28px;text-align:center;color:var(--ink)}
.field{height:38px;border:1px solid #ddd;margin-top:16px;font-size:12px;color:#aaa;padding:11px 14px 0 40px;position:relative}
.field::before{content:"";position:absolute;left:14px;top:13px;width:11px;height:11px;background:var(--gold);border-radius:2px}

/* footer */
.footer-nav{position:absolute;left:0;width:1200px;top:3950px;display:flex;justify-content:center;gap:48px;font-size:16px;color:var(--ink)}
.socials{position:absolute;left:0;width:1200px;top:4015px;display:flex;justify-content:center;gap:14px}
.socials span{width:30px;height:30px;border-radius:50%;border:2px solid var(--gold)}
.copy{position:absolute;left:0;width:1200px;top:4078px;text-align:center;font-size:12px;color:var(--muted)}
</style>
</head>
<body>

<section class="hero" role="img" aria-label="Photo of happy friends laughing together outdoors at sunset"></section>
<div class="brand"><span class="brand-square"></span>condara</div>
<div class="topbar">
  <span class="phone"><svg width="18" height="18" viewBox="0 0 24 24"><path fill="#e3a21a" d="M6.6 10.8a15 15 0 0 0 6.6 6.6l2.2-2.2a1 1 0 0 1 1-.25 11.4 11.4 0 0 0 3.6.6 1 1 0 0 1 1 1V20a1 1 0 0 1-1 1A17 17 0 0 1 3 4a1 1 0 0 1 1-1h3.5a1 1 0 0 1 1 1c0 1.25.2 2.45.6 3.6a1 1 0 0 1-.25 1z"/></svg>Phone : 1 555 010 2040</span>
  <span class="login"><i><svg width="16" height="16" viewBox="0 0 24 24"><circle cx="12" cy="8" r="4" fill="#e3a21a"/><path d="M4 21c0-4.4 3.6-7 8-7s8 2.6 8 7z" fill="#e3a21a"/></svg></i>Member Login</span>
</div>
<div class="arrow" style="left:40px"></div>
<div class="arrow" style="right:40px"></div>
<h1 class="hero-title serif">CONDARA</h1>
<p class="hero-sub">Sed ut perspiciatis unde omnis iste natus error sit voluptatem accusantium</p>
<span class="btn btn-gold" style="left:438px;top:585px;width:130px;height:44px;z-index:2">Read More</span>
<span class="btn btn-ghost" style="left:588px;top:585px;width:170px;height:44px;z-index:2">News &amp; Events</span>

<div class="menu-shadow"></div>
<nav class="menu">
  <span>Home</span><span>About us</span><span>Services</span><span>News &amp; Events</span><span>Contact us</span>
  <span class="search">Search...</span>
</nav>

<!-- About -->
<h2 class="h2" style="left:100px;top:945px">About us</h2>
<span class="mark" style="left:104px;top:1020px"></span>
<p class="body-text" style="left:100px;top:1060px;width:440px">Sed ut perspiciatis unde omnis iste natus error sit voluptatem accusantium doloremque laudantium, totam rem aperiam, eaque ipsa quae ab illo inventore veritatis et quasi architecto beatae vitae dicta sunt explicabo. Nemo enim ipsam voluptatem quia voluptas sit aspernatur aut odit aut fugit, sed quia consequuntur magni dolores eos qui ratione voluptatem sequi nesciunt. Neque porro quisquam est, qui dolorem ipsum quia dolor sit amet, consectetur, adipisci velit, sed quia non numquam eius modi tempora incidunt.</p>
<span class="btn btn-gold" style="left:100px;top:1328px;width:140px;height:44px">Read More</span>
<div class="frame" style="left:600px;top:960px;width:470px;height:420px"></div>
<div class="photo" role="img" aria-label="Photo of business people in a meeting around a conference table" style="left:620px;top:980px;width:480px;height:400px;background:linear-gradient(135deg,#d9dde2,#8c939b 60%,#3e4248)"></div>

<!-- News -->
<div class="news-band"></div>
<h2 class="h2" style="left:0;width:1200px;text-align:center;top:1712px;font-weight:400">News &amp; Events</h2>
<span class="mark" style="left:593px;top:1785px"></span>
<article class="card" style="left:100px;top:1870px;width:450px;height:435px">
  <div role="img" aria-label="Photo of two businessmen walking outside an office building" style="height:280px;background:linear-gradient(135deg,#bfc3c7,#5d6166 60%,#2c2e31)"></div>
  <div style="padding:22px 22px">
    <h3>Quia non numquam eius nostrum accusantium</h3>
    <div class="date">July 10, 2018</div>
    <p>Sed ut perspiciatis unde omnis iste natus error sit voluptatem accusantium doloremque.</p>
  </div>
</article>
<article class="card" style="left:575px;top:1870px;width:525px;height:195px;display:flex">
  <div role="img" aria-label="Photo of a businessman and businesswoman shaking hands" style="width:175px;height:175px;margin:10px;background:linear-gradient(135deg,#d6d6d6,#7d7f82)"></div>
  <div style="padding:24px 14px"><h3>Quia noaccusantiumnumqua nostrum accu santium</h3><div class="date">July 10, 2018</div><p>Sed ut perspiciatis unde omnis iste natus error sit voluptatem accusantium doloremque.</p></div>
</article>
<article class="card" style="left:575px;top:2100px;width:525px;height:195px;display:flex">
  <div role="img" aria-label="Photo of a team working at a desk with laptops" style="width:175px;height:175px;margin:10px;background:linear-gradient(135deg,#e0ddd8,#8a847d)"></div>
  <div style="padding:24px 14px"><h3>Quia noaccusantiumnumqua nostrum accu santium</h3><div class="date">July 10, 2018</div><p>Sed ut perspiciatis unde omnis iste natus error sit voluptatem accusantium doloremque.</p></div>
</article>
<span class="btn btn-gold" style="left:505px;top:2365px;width:190px;height:46px">View All News</span>

<!-- Testimonials -->
<h2 class="h2" style="left:0;width:1200px;text-align:center;top:2655px;font-weight:400">Client Testimonials</h2>
<span class="mark" style="left:593px;top:2728px"></span>
<p class="body-text" style="left:210px;top:2780px;width:780px;text-align:center;font-size:13px">Sed ut perspiciatis unde omnis iste natus error sit voluptatem accusantium doloremque laudantium, totam rem aperiam, eaque ipsa quae ab illo inventore veritatis et quasi architecto beatae vitae dicta sunt explicabo. Nemo enim ipsam voluptatem quia voluptas sit aspernatur aut odit aut fugit, sed quia consequuntur magni dolores eos qui ratione voluptatem sequi nesciunt.</p>
<p class="abs" style="left:0;width:1200px;top:2900px;text-align:center;font-size:14px;font-weight:700">- Quis nostrum <span style="color:var(--gold);letter-spacing:2px">★★★★★</span></p>
<svg class="abs" style="left:576px;top:2944px" width="48" height="16" viewBox="0 0 48 16"><path d="M10 2 4 8l6 6" stroke="#e3a21a" stroke-width="2.5" fill="none"/><path d="M38 2l6 6-6 6" stroke="#2b2b2b" stroke-width="2.5" fill="none"/></svg>

<!-- Contact -->
<div class="dark" role="img" aria-label="Dark background with a faint world map"></div>
<h2 class="h2" style="left:100px;top:3300px;font-size:38px;color:var(--white)">Contact us</h2>
<span class="mark" style="left:104px;top:3360px"></span>
<p class="body-text" style="left:100px;top:3390px;width:440px;color:#bdbdbd;font-size:13px;line-height:22px">Sed ut perspiciatis unde omnis iste natus error sit voluptatem accusantium doloremque laudantium, totam rem aperiam.</p>
<div class="contact-item" style="left:100px;top:3462px;width:440px"><i><svg width="16" height="20" viewBox="0 0 24 30"><path d="M12 0a10 10 0 0 0-10 10c0 8 10 20 10 20s10-12 10-20A10 10 0 0 0 12 0zm0 14a4 4 0 1 1 0-8 4 4 0 0 1 0 8z" fill="#fff"/></svg></i>1234 Nemo enim ipsam voluptatem quia voluptas sit aspernatur aut odit</div>
<div class="contact-item" style="left:100px;top:3528px"><i><svg width="16" height="16" viewBox="0 0 24 24"><path fill="#fff" d="M6.6 10.8a15 15 0 0 0 6.6 6.6l2.2-2.2a1 1 0 0 1 1-.25 11.4 11.4 0 0 0 3.6.6 1 1 0 0 1 1 1V20a1 1 0 0 1-1 1A17 17 0 0 1 3 4a1 1 0 0 1 1-1h3.5a1 1 0 0 1 1 1c0 1.25.2 2.45.6 3.6a1 1 0 0 1-.25 1z"/></svg></i>Phone : 1 555 010 2040</div>

<form class="form">
  <h3>Say Hello To Condara</h3>
  <div style="width:40px;height:3px;background:var(--gold);margin:14px auto 24px"></div>
  <div class="field">Enter Name</div>
  <div class="field">Enter Email</div>
  <div class="field">Subject</div>
  <div class="field" style="height:90px">Message</div>
  <div class="btn btn-gold" style="position:relative;margin-top:26px;height:42px;border-radius:2px">Submit Message</div>
</form>

<!-- Footer -->
<div class="abs" style="left:0;top:3610px;width:1200px;height:554px;background:linear-gradient(180deg,#fffaf0,#ffffff 60%)"></div>
<div class="abs serif" style="left:0;width:1200px;top:3740px;display:flex;justify-content:center;align-items:center;gap:14px;font-family:'Lato',sans-serif;font-size:46px;font-weight:700;color:var(--ink)"><span style="width:40px;height:40px;background:var(--gold)"></span>condara</div>
<nav class="footer-nav"><span>Home</span><span>About us</span><span>Services</span><span>News &amp; Events</span><span>Contact us</span></nav>
<div class="socials"><span></span><span></span><span></span><span></span><span></span><span></span><span></span></div>
<p class="copy">Copyright © Condara, 2018 All Rights Reserved</p>

</body>
</html>
```